A new fresh and flat K&T Logistics Brochure Design A4 - 4 pages

Our client is an established International Logistics firm looking to upgrade their sales brochure.
We would like the designer to create concepts that are flat, modern and communicate reliability and expediency to our clients. We want the brochure to maintain a degree of white space and minimal design.
Introduction
LOGISTICS - it's what we do best! We're proud to say so after 27 years (and counting) of organic growth within the 3PL industry. Starting off in Meridian, Mississippi with a fleet of 4 trucks in 1987, K&T is today a global 3PL company with offices in the United States and Asia Pacific region.
Our goal has always been to serve our clients by getting things done, and getting them done right.
Format: A4 4-sided brochure
Pg 1 Front Page - Company name and logo, and vector design concept to make front page unique. Please try to include some kind of container reference design on the front page (e.g 2D or 3D vector, transparent overlay etc...), place this design element somewhere in the middle or bttom of the page.
Pg 2 and/or Pg 3
- Introduction and Core services Including: ABOUT, SERVICES, CONTRACT LOGISTICS, K&T INTEL (following the menu content of our website www.ktvfr.example)
- Text space to explain Services in more detail.
Social proof (existing client testimonials/feedback.)
- A 'C.A.R.E' acronym design element, including the words: Communicative, Accessible, Responsible, Efficient
Pg 4 Back Page- Contact information, Call to action.
Throughut the brochure please leave space for images as you deem appropriate and we will update late OR even better usesome of your own stock images.
Color theme: Based on corporate colors (but not limited to), see website
http://www.ktvfr.example
Try diffent font types to the website both serif and sans serif
Include several CTAs throughout the brochure.
You can use both the attached pdf brochure and the website for content.
We would also appreciate if you could also enhance the logo to make it 'pop' (keep shape and style).

```html
<!DOCTYPE html>
<html lang="en">
<head>
<meta charset="utf-8">
<title>K&amp;T Logistics – Brochure Spread</title>
<link href="https://fonts.googleapis.com/css2?family=Barlow:wght@400;500&family=Barlow+Condensed:wght@500;600;700&display=swap" rel="stylesheet">
<style>
  :root {
    --slate: #7b93ad;
    --orange: #f39a1e;
    --navy: #1f3b82;
    --ink: #2a2a2a;
    --white: #ffffff;
    --mist: #c9d2dc;
    --hatch: #eef0f2;
  }
  * { margin: 0; padding: 0; box-sizing: border-box; }
  html, body { width: 1200px; height: 849px; overflow: hidden; background: var(--white); }
  .spread { position: relative; width: 1200px; height: 849px; font-family: "Barlow", Arial, sans-serif; }

  .panel-left { position: absolute; left: 0; top: 0; width: 738px; height: 849px; background: var(--slate); }
  .band-top { position: absolute; left: 400px; top: 0; width: 800px; height: 40px; background: linear-gradient(90deg, rgba(238,240,242,0) 0%, var(--hatch) 45%); }
  .band-bottom { position: absolute; left: 738px; top: 800px; width: 462px; height: 49px; background: var(--hatch); }

  .on-slate { color: var(--white); }

  .mission { position: absolute; left: 68px; top: 60px; width: 400px; }
  .quote-mark { position: absolute; left: 0; top: 4px; font-family: "Barlow Condensed", sans-serif; font-weight: 700; font-size: 92px; line-height: 1; color: var(--orange); }
  .mission h2 { margin-left: 69px; font-family: "Barlow Condensed", sans-serif; font-weight: 600; font-size: 21px; line-height: 24px; }
  .mission p { margin-left: 69px; font-size: 10.6px; line-height: 14.6px; width: 318px; letter-spacing: -0.1px; }

  .photo { position: absolute; }
  .photo-warehouse { left: 0; top: 185px; width: 738px; height: 292px; background: linear-gradient(180deg, #5a6470 0%, #b9a184 55%, #8a8378 100%); }
  .photo-port { left: 772px; top: 558px; width: 189px; height: 110px; background: linear-gradient(180deg, #c98a55 0%, #5d6a7c 100%); }
  .photo-plane { left: 964px; top: 558px; width: 193px; height: 110px; background: linear-gradient(135deg, #8fa7c2 0%, #d8dde2 100%); }
  .photo-dock { left: 772px; top: 670px; width: 385px; height: 120px; background: linear-gradient(90deg, #b3403c 0%, #9eaebf 50%, #d9a04e 100%); }

  .about-title { position: absolute; left: 137px; top: 494px; font-family: "Barlow Condensed", sans-serif; font-weight: 600; font-size: 38px; line-height: 40px; color: var(--orange); }
  .about-col { position: absolute; font-size: 10.6px; line-height: 14.6px; letter-spacing: -0.1px; }
  .about-col p + p { margin-top: 14px; }
  .about-col-a { left: 137px; top: 535px; width: 208px; }
  .about-col-b { left: 354px; top: 500px; width: 205px; }

  .care { position: absolute; left: 40px; top: 722px; font-family: "Barlow Condensed", sans-serif; font-weight: 600; font-size: 58px; line-height: 46px; color: var(--mist); transform: scaleX(0.87); transform-origin: left top; white-space: nowrap; }
  .care .line { display: block; }
  .care .line-2 { margin-left: 98px; }
  .care .initial { color: var(--orange); }

  .services-intro { position: absolute; left: 771px; top: 117px; width: 400px; font-family: "Barlow Condensed", sans-serif; font-weight: 600; font-size: 21px; line-height: 21px; color: var(--orange); }
  .service { position: absolute; color: var(--ink); }
  .service h3 { font-family: "Barlow Condensed", sans-serif; font-weight: 600; font-size: 33px; line-height: 31px; color: var(--navy); margin-bottom: 7px; }
  .service p { font-size: 10.4px; line-height: 14.7px; letter-spacing: -0.1px; }
  .service-sea { left: 771px; top: 200px; width: 182px; }
  .service-air { left: 771px; top: 426px; width: 182px; }
  .service-road { left: 969px; top: 200px; width: 200px; }
</style>
</head>
<body>
<div class="spread">
  <div class="panel-left"></div>
  <div class="band-top"></div>
  <div class="band-bottom"></div>

  <section class="mission on-slate">
    <span class="quote-mark">&ldquo;</span>
    <h2>Mission Statement</h2>
    <p>Customer focus, innovation, and operational excellence are the driving forces behind our aim to provide fully integrated logistics solutions. Dedication, quality of service, and the expertise of our personnel are the asset base we draw upon to strive to be not just a partner, but an extension of our clients' business.</p>
  </section>

  <div class="photo photo-warehouse" role="img" aria-label="Warehouse aisle with tall pallet racking stacked with boxes"></div>

  <h2 class="about-title">ABOUT US</h2>
  <div class="about-col about-col-a on-slate">
    <p>With roots in the US Road Transportation Industry, K&amp;T has evolved over the last 25 years from being a regional road transportation company to a global provider of leading, innovative, and fully integrated supply chain logistics and management.</p>
    <p>Founded in Meridian, MS in 1987, K&amp;T began its business in the road transportation industry. With a fleet of over 30 trucks servicing the greater American South East,</p>
  </div>
  <div class="about-col about-col-b on-slate">
    <p>K&amp;T has expanded its base over the years to evolve into a provider of International Road, Rail, Sea and Air transportation.</p>
    <p>The rapid development of global trade over the last decade has also seen K&amp;T specialize in 3PL and 4PL management of warehousing and distribution, customs brokerage, and industry specific supply chain consulting. Today K&amp;T has offices in the Greater United States and Asia Pacific region as well as a worldwide network of trusted partners that ensure we are globally present to serve our clients requirements.</p>
  </div>

  <div class="care" aria-label="Communicative Accessible Responsible Efficient">
    <span class="line line-1"><span class="initial">C</span>OMMUNICATIVE <span class="initial">A</span>CCESSIBLE</span>
    <span class="line line-2"><span class="initial">R</span>ESPONSIBLE <span class="initial">E</span>FFICIENT</span>
  </div>

  <h2 class="services-intro">Our dedicated team of industry experts has helped us attain respectable market positions in the following logistics services:</h2>

  <section class="service service-sea">
    <h3>SEAFREIGHT</h3>
    <p>Equipped to handle Port-to-Port or Multimodal shipments to all regions across the globe, K&amp;T is your one stop shop for any and all of your sea freight needs! As a licensed NVOCC, we take pride in the responsibility you place in our hands to handle your shipments with the utmost of diligence and efficiency. Whether you're in need of shipping Containerized, LCL, or Project cargo, look no further than K&amp;T to do justice to your shipping requirements</p>
  </section>

  <section class="service service-air">
    <h3>AIRFREIGHT</h3>
    <p>With strong tie ups to major air carriers, and a trusted network of partners at most global airports, we're confident in our ability to deliver on your time sensitive shipments.</p>
  </section>

  <section class="service service-road">
    <h3>ROAD &amp; RAIL<br>LOGISTICS</h3>
    <p>With over 25 years of experience in the trucking business and a fleet thats grown organically from 4 trucks in 1987, to over 30 trucks in 2013, we're proud of the inroads we have made in the trucking sector. We're equipped to truck anywhere in the 48 contiguous states of the USA and if you need trucking outside the US - we've got long-standing partners in most of continental Europe as well as infrastructure in China that helps ensure we're present globally to cover your land transportation requirements. Freight &amp; Transportation Freight &amp; Transportation Warehousing &amp; Distribution Fulfillment &amp; Retail K&amp;T Intel</p>
  </section>

  <div class="photo photo-port" role="img" aria-label="Container port cranes at sunset"></div>
  <div class="photo photo-plane" role="img" aria-label="Cargo aircraft being loaded"></div>
  <div class="photo photo-dock" role="img" aria-label="Loading dock doors with forklift and container truck"></div>
</div>
</body>
</html>
```